RW Framewell Inc Business cards

We need business cards using our existing logo but slightly modified. Right now the logo says RW Loadbearing Masonry. We want to keep the RW part of the design, but replace the Structural Concrete portion with "FRAMEWELL". Please see the attached file.
Ideally this would be a blank template so we can add Different Names, titles, and phone numbers later.
On the one side we want only the logo and on the other side the detail. I'm attaching an example for you to see.
Please reach out with any other questions. Our address and other details will be given out once we find a design we like.

Target Market(s)

Construction Industry

```html
<!DOCTYPE html>
<html lang="en">
<head>
<meta charset="utf-8">
<title>RW Framewell Inc – Business Cards</title>
<link rel="stylesheet" href="https://fonts.googleapis.com/css2?family=Archivo:wght@400;800&family=Arimo:wght@400&display=swap">
<style>
  :root {
    --canvas: #2a2b2d;
    --card: #1c1d1f;
    --card-pattern-top: #26272a;
    --blue: #1a77c7;
    --grey: #8c8d90;
    --grey-light: #b9babd;
    --rule: #6f7073;
  }
  html, body {
    margin: 0;
    width: 1200px;
    height: 1108px;
    overflow: hidden;
    background: var(--canvas);
  }
  .canvas {
    position: relative;
    width: 1200px;
    height: 1108px;
  }
  .card {
    position: absolute;
    top: 200px;
    width: 420px;
    height: 700px;
    border-radius: 22px;
    background: var(--card);
    box-shadow: 0 18px 40px rgba(0,0,0,.45);
    overflow: hidden;
  }
  .card--front { left: 150px; }
  .card--back { left: 630px; }

  .brand {
    position: absolute;
    left: 0; right: 0;
    top: 150px;
    text-align: center;
    font-family: "Archivo", sans-serif;
    font-weight: 800;
    color: var(--blue);
    line-height: 1;
  }
  .brand__initials { display: block; font-size: 150px; letter-spacing: 4px; }
  .brand__name { display: block; font-size: 40px; letter-spacing: 3px; margin-top: 6px; }

  .person {
    position: absolute;
    left: 0; right: 0;
    top: 430px;
    text-align: center;
  }
  .person__name {
    margin: 0;
    font-family: "Archivo", sans-serif;
    font-weight: 800;
    font-size: 30px;
    color: var(--blue);
    letter-spacing: .5px;
  }
  .person__title {
    margin: 4px 0 0;
    font-family: "Arimo", sans-serif;
    font-size: 20px;
    color: var(--grey-light);
  }
  .contact-rule {
    display: flex;
    align-items: center;
    justify-content: center;
    gap: 8px;
    margin: 20px auto 14px;
    width: 300px;
  }
  .contact-rule__line { flex: 1; height: 1px; background: var(--rule); }
  .contact-rule__icon {
    width: 28px; height: 28px;
    border-radius: 4px;
    background: var(--blue);
    display: flex; align-items: center; justify-content: center;
  }
  .contact-list {
    margin: 0; padding: 0; list-style: none;
    font-family: "Arimo", sans-serif;
    font-size: 20px;
    line-height: 1.4;
    color: var(--grey-light);
  }

  .back-pattern {
    position: absolute;
    inset: 0 0 35% 0;
    background: linear-gradient(to bottom, var(--card-pattern-top), var(--card));
  }
  .back-mark {
    position: absolute;
    left: 0; right: 0;
    top: 460px;
    text-align: center;
    font-family: "Archivo", sans-serif;
    font-weight: 800;
    font-size: 60px;
    letter-spacing: 2px;
    color: var(--blue);
  }
</style>
</head>
<body>
<main class="canvas">
  <section class="card card--front" aria-label="Card front">
    <div class="brand">
      <span class="brand__initials">RW</span>
      <span class="brand__name">FRAMEWELL</span>
    </div>
    <div class="person">
      <h1 class="person__name">DANIEL HARTLEY</h1>
      <p class="person__title">Managing Director</p>
      <div class="contact-rule">
        <span class="contact-rule__line"></span>
        <span class="contact-rule__icon">
          <svg width="16" height="16" viewBox="0 0 16 16" aria-hidden="true"><path d="M3 2h3l1 3-2 1a8 8 0 0 0 5 5l1-2 3 1v3a1 1 0 0 1-1 1A12 12 0 0 1 2 3a1 1 0 0 1 1-1z" fill="#1c1d1f"/></svg>
        </span>
        <span class="contact-rule__icon">
          <svg width="16" height="16" viewBox="0 0 16 16" aria-hidden="true"><rect x="1.5" y="3.5" width="13" height="9" fill="none" stroke="#1c1d1f" stroke-width="1.5"/><path d="M1.5 3.5 8 9l6.5-5.5" fill="none" stroke="#1c1d1f" stroke-width="1.5"/></svg>
        </span>
        <span class="contact-rule__icon">
          <svg width="16" height="16" viewBox="0 0 16 16" aria-hidden="true"><circle cx="8" cy="8" r="6.5" fill="none" stroke="#1c1d1f" stroke-width="1.5"/><ellipse cx="8" cy="8" rx="3" ry="6.5" fill="none" stroke="#1c1d1f" stroke-width="1.2"/><path d="M1.5 8h13" stroke="#1c1d1f" stroke-width="1.2"/></svg>
        </span>
        <span class="contact-rule__line"></span>
      </div>
      <ul class="contact-list">
        <li>044-870 315 622</li>
        <li>info@rwframewell.com</li>
        <li>www.rwframewell.com</li>
      </ul>
    </div>
  </section>

  <section class="card card--back" aria-label="Card back">
    <div class="back-pattern" role="img" aria-label="Faint repeated brand pattern across the upper card"></div>
    <div class="back-mark">RW</div>
  </section>
</main>
</body>
</html>
```